Veldmark Supplies Business Card

Professional business card that stand out to our potential customers. Front and back with clean modern design

Industry/Entity Type

Oil and gas

Contact Information for Business Card

Name, address, website , office phone and cell number

Requirements
Must have
• Editable files for each employee

```html
<!DOCTYPE html>
<html lang="en">
<head>
<meta charset="utf-8">
<title>Veldmark Supplies Business Card</title>
<link href="https://fonts.googleapis.com/css2?family=Poppins:wght@300;400;600;800&display=swap" rel="stylesheet">
<style>
  :root {
    --brand-red: #e8262a;
    --brand-blue: #13afd1;
    --ink: #1c1c1c;
    --paper: #ffffff;
    --backdrop: #e4e8e9;
  }
  * { margin: 0; padding: 0; box-sizing: border-box; }
  html, body { width: 1200px; height: 960px; overflow: hidden; }
  body {
    background: var(--backdrop);
    font-family: "Poppins", sans-serif;
    position: relative;
  }
  .card {
    position: absolute;
    left: 250px;
    width: 701px;
    height: 400px;
    background: var(--paper);
    border-left: 4px solid var(--brand-blue);
    border-bottom: 3px solid var(--brand-blue);
  }
  .card--front { top: 60px; }
  .card--back { top: 500px; }

  .brand {
    position: absolute;
    display: flex;
    align-items: center;
    gap: 14px;
    color: var(--brand-red);
    font-weight: 800;
    text-transform: uppercase;
    white-space: nowrap;
  }
  .brand__square { background: var(--brand-red); flex: none; }
  .card--front .brand {
    left: 50%; top: 50%;
    transform: translate(-50%, -50%);
    font-size: 40px;
    letter-spacing: 1px;
  }
  .card--front .brand__square { width: 48px; height: 48px; }
  .card--back .brand {
    left: 165px; top: 200px;
    transform: translate(-50%, -50%);
    font-size: 24px;
    letter-spacing: 0.5px;
    gap: 10px;
  }
  .card--back .brand__square { width: 30px; height: 30px; }

  .divider {
    position: absolute;
    left: 346px; top: 66px;
    width: 1px; height: 269px;
    background: var(--brand-blue);
  }
  .contact {
    position: absolute;
    left: 397px; top: 82px;
  }
  .contact__name {
    font-size: 33px;
    line-height: 1;
    white-space: nowrap;
  }
  .contact__first { color: var(--brand-red); font-weight: 600; }
  .contact__last { color: var(--brand-blue); font-weight: 300; }
  .contact__role {
    margin-top: 8px;
    font-size: 17px;
    color: var(--ink);
  }
  .contact__address {
    margin-top: 14px;
    font-size: 17px;
    line-height: 24px;
    color: var(--brand-red);
    font-style: normal;
  }
  .contact__list { list-style: none; margin-top: 14px; }
  .contact__item {
    display: flex;
    align-items: center;
    height: 23.5px;
    font-size: 18px;
    color: var(--ink);
  }
  .contact__icon { width: 16px; height: 16px; margin-right: 13px; flex: none; }
</style>
</head>
<body>
  <section class="card card--front">
    <div class="brand"><span class="brand__square"></span>Veldmark Supplies</div>
  </section>

  <section class="card card--back">
    <div class="brand"><span class="brand__square"></span>Veldmark Supplies</div>
    <div class="divider"></div>
    <div class="contact">
      <h1 class="contact__name"><span class="contact__first">Lena</span> <span class="contact__last">Horvatova</span></h1>
      <p class="contact__role">Co-Founder &amp; CEO</p>
      <address class="contact__address">2480 Millbrook Lane,<br>Ridgefield, WI 53190</address>
      <ul class="contact__list">
        <li class="contact__item">
          <svg class="contact__icon" viewBox="0 0 16 16"><path d="M3 1.5l3 .5 1 3.5-2 1.5c1 2 2.5 3.5 4.5 4.5l1.5-2 3.5 1 .5 3c-1 1-2.5 1.5-4 1C6 13 3 10 1.5 5 1 3.5 1.5 2.5 3 1.5z" fill="var(--brand-blue)"/></svg>
          (814) 620-3147
        </li>
        <li class="contact__item">
          <svg class="contact__icon" viewBox="0 0 16 16"><rect x="3.5" y="1" width="9" height="14" rx="1.5" fill="none" stroke="var(--brand-red)" stroke-width="1.6"/></svg>
          (555) 410-3147
        </li>
        <li class="contact__item">
          <svg class="contact__icon" viewBox="0 0 16 16"><circle cx="8" cy="8" r="7" fill="var(--brand-blue)"/><path d="M8 1v14M1 8h14" stroke="#fff" stroke-width="0.8"/></svg>
          www.website.com
        </li>
        <li class="contact__item">
          <svg class="contact__icon" viewBox="0 0 16 16"><rect x="1" y="4" width="14" height="10" fill="var(--brand-red)"/><path d="M1 4l7 5 7-5" fill="none" stroke="#fff" stroke-width="1"/></svg>
          info@website.com
        </li>
      </ul>
    </div>
  </section>
</body>
</html>
```